Website Design Request - Management Consulting Firm

We need a Website designed for an IT Management Staffing and Recruiting firm called TRAVENOK based in San Francisco.

The firm is an high-end technology staffing agency. Our focus is on quality and high-caliber candidates rather than quantity.

The website will have two main home pages. One for the recruiter and another on for the candidates.

The website needs to optimize for mobile devices as well.

I have attached few mock-ups that I have done just to show what I am thinking. The UI needs to be very clean, fluid, and it needs to have a modern, rustic, professional feel to it.

Target Market(s)

Technology Manager, Director, VP, CIO of Companies that have $4b-10b dollar revenue. Such as larkspurdwellings.example , https://www.velmorian.example/, quillnet.example, zib.example

Industry/Entity Type

Management Consulting

Number of Pages Required

5+ page

Font styles to use
Sans Serif

Colors
f37122
ffffff

Requirements
Must have
• Please review mock-ups for suggestions
Nice to have
Should not have

```html
<!DOCTYPE html>
<html lang="en">
<head>
<meta charset="utf-8">
<title>TRAVENOK – Project Management Consulting</title>
<link href="https://fonts.googleapis.com/css2?family=Jost:wght@300;400;500;600&display=swap" rel="stylesheet">
<style>
:root{
  --brand:#f37122;
  --white:#ffffff;
  --ink:#222222;
  --text:#555555;
  --muted:#8a8a8a;
  --line:#e4e4e4;
  --footer-bg:#f3f3f3;
  --ghost:#f1f1f1;
}
*{box-sizing:border-box;margin:0;padding:0}
html,body{width:1200px;height:2253px;overflow:hidden;background:var(--white)}
body{position:relative;font-family:"Jost",Arial,sans-serif;color:var(--ink)}
.abs{position:absolute}

/* header */
.site-header{position:absolute;left:0;top:0;width:1200px;height:111px;background:var(--white)}
.brand{position:absolute;left:132px;top:14px}
.brand-name{font-size:48px;font-weight:500;color:var(--brand);letter-spacing:2px;line-height:1}
.brand-tag{font-size:12.5px;color:var(--ink);letter-spacing:.6px;margin-top:4px;text-transform:uppercase}
.nav-link{position:absolute;top:40px;font-size:16px;font-weight:500;color:var(--ink)}
.btn-outline,.btn-solid{position:absolute;top:32px;height:36px;font-size:16px;display:flex;align-items:center;justify-content:center;gap:8px}
.btn-outline{left:837px;width:102px;border:1.5px solid var(--brand);color:var(--brand)}
.btn-solid{left:966px;width:100px;background:var(--brand);color:var(--white)}

/* hero */
.hero{position:absolute;left:0;top:111px;width:1200px;height:554px;overflow:hidden}
.hero-photo{position:absolute;inset:0;background:linear-gradient(120deg,#8d8a86 0%,#b9b5ae 35%,#a8a6a2 60%,#7e7c7a 100%)}
.hero-shade{position:absolute;inset:0;background:rgba(30,30,30,.38)}
.hero-title{position:absolute;left:0;width:1200px;top:80px;text-align:center;color:var(--white);font-size:40px;font-weight:500}
.hero-sub{position:absolute;left:0;width:1200px;top:136px;text-align:center;color:var(--white);font-size:21px}
.search-field{position:absolute;left:186px;top:232px;width:582px;height:68px;background:var(--white);border:2px solid #ccc;outline:2px solid var(--white);outline-offset:2px;display:flex;align-items:center;padding-left:30px;gap:18px;font-size:14px;color:var(--ink)}
.cta{position:absolute;left:780px;top:232px;width:240px;height:68px;background:var(--brand);color:var(--white);font-size:21px;font-weight:500;display:flex;align-items:center;justify-content:center}
.terms{position:absolute;left:186px;top:320px;color:var(--white);font-size:15px}
.terms b{font-weight:600;text-decoration:underline}
.job-line{position:absolute;left:0;width:1200px;top:462px;display:flex;justify-content:center;align-items:center;gap:10px;color:var(--white);font-size:15px}
.job-line span.tag{background:var(--brand);padding:5px 9px}

/* tabs */
.tab{position:absolute;top:718px;width:249px;height:62px;border:1.5px solid #555;display:flex;align-items:center;justify-content:center;gap:12px;font-size:20px;color:var(--ink)}
.tab.active{border-color:var(--brand);color:var(--brand)}
.tab.active::after{content:"";position:absolute;bottom:-8px;left:50%;margin-left:-7px;width:14px;height:14px;background:var(--white);border-right:1.5px solid var(--brand);border-bottom:1.5px solid var(--brand);transform:rotate(45deg)}

/* steps */
.section-intro{position:absolute;left:0;width:1200px;top:853px;text-align:center;font-size:17px;color:var(--text);font-weight:300}
.intro-rule{position:absolute;left:512px;top:902px;width:146px;height:4px;background:var(--line)}
.backdrop{position:absolute;left:305px;top:1060px;width:590px;height:790px;border-radius:300px 300px 120px 200px;background:linear-gradient(90deg,#f8efe9 0%,#f4f4f4 50%,#fbf3ee 100%);opacity:.8}
.step-circle{position:absolute;width:134px;height:134px;border-radius:50%;background:var(--white);border:1.5px solid #dcdcdc;display:flex;align-items:center;justify-content:center}
.step-label{position:absolute;font-size:12px;font-weight:600;letter-spacing:1px;color:var(--ink)}
.step-title{position:absolute;left:0;width:1200px;text-align:center;font-size:17px;font-weight:500;color:var(--ink)}
.step-text{position:absolute;left:0;width:1200px;text-align:center;font-size:13.5px;line-height:1.5;color:var(--text);font-weight:300}
.pill{position:absolute;left:555px;top:1868px;width:90px;height:30px;border-radius:15px;background:var(--ghost)}
.flow{position:absolute;left:0;top:0}

/* footer */
.site-footer{position:absolute;left:0;top:1957px;width:1200px;height:296px;background:var(--footer-bg)}
.footer-brand{position:absolute;left:132px;top:58px}
.footer-brand .brand-name{font-size:54px}
.footer-brand .brand-tag{font-size:14px}
.footer-head{position:absolute;top:55px;font-size:14px;font-weight:600;color:var(--brand);text-transform:uppercase}
.contact-row{position:absolute;left:558px;display:flex;gap:18px;font-size:12.5px;color:var(--text);line-height:24px}
.social{position:absolute;top:2047px;width:43px;height:43px;border-radius:50%;background:var(--white);border:1.5px solid #4a5aa8}
.footer-rule{position:absolute;left:132px;top:206px;width:936px;height:1px;background:#dddddd}
.copyright{position:absolute;left:0;width:1200px;top:244px;text-align:center;font-size:11.5px;color:var(--text)}
</style>
</head>
<body>

<header class="site-header">
  <div class="brand">
    <div class="brand-name">TRAVENOK</div>
    <div class="brand-tag">Project Management Consulting</div>
  </div>
  <span class="nav-link" style="left:602px">Professionals</span>
  <span class="nav-link" style="left:732px">Employers</span>
  <a class="btn-outline">
    <svg width="12" height="14" viewBox="0 0 12 14"><rect x="1" y="6" width="10" height="8" fill="#f37122"/><path d="M3 6V4a3 3 0 0 1 6 0v2" stroke="#f37122" stroke-width="1.8" fill="none"/></svg>
    Sign In
  </a>
  <a class="btn-solid">
    <svg width="14" height="14" viewBox="0 0 14 14"><rect x="1" y="2" width="10" height="11" fill="none" stroke="#fff" stroke-width="1.5"/><path d="M6 8l6-6" stroke="#fff" stroke-width="2"/></svg>
    Sign Up
  </a>
</header>

<section class="hero">
  <div class="hero-photo" role="img" aria-label="Photo of a smiling team of business professionals in a bright office"></div>
  <div class="hero-shade"></div>
  <h1 class="hero-title">FILL IT PROJECT MANAGEMENT POSITIONS FAST</h1>
  <p class="hero-sub">Search our network and hire TOP IT PM Talents for permanent &amp; contract roles</p>
  <div class="search-field">
    <svg width="12" height="13" viewBox="0 0 12 13"><circle cx="6" cy="3.5" r="3" fill="#222"/><path d="M0 13c0-4 2.5-6 6-6s6 2 6 6z" fill="#222"/></svg>
    IT PROJECT MANAGER
  </div>
  <div class="cta">GET STARTED</div>
  <p class="terms">By entering your email address, you agree to our <b>Terms &amp; conditions</b></p>
  <p class="job-line">Looking for a Job? <span class="tag">Upload Resume</span> and let companies send you others</p>
</section>

<nav>
  <div class="tab" style="left:202px">
    <svg width="16" height="16" viewBox="0 0 16 16"><circle cx="6.5" cy="6.5" r="5" stroke="#222" stroke-width="2" fill="none"/><path d="M10 10l5 5" stroke="#222" stroke-width="2.2"/></svg>
    Our Focus
  </div>
  <div class="tab" style="left:475px">
    <svg width="18" height="18" viewBox="0 0 18 18"><circle cx="9" cy="8" r="7" fill="#f37122"/><rect x="6" y="14" width="6" height="4" fill="#444"/></svg>
    Why us?
  </div>
  <div class="tab active" style="left:749px">
    <svg width="16" height="16" viewBox="0 0 16 16"><circle cx="8" cy="8" r="5" fill="none" stroke="#f37122" stroke-width="3.5" stroke-dasharray="3 1.6"/><circle cx="8" cy="8" r="2" fill="#f37122"/></svg>
    How it Works?
  </div>
</nav>

<main>
  <p class="section-intro">Fast track your hiring with three simple steps</p>
  <div class="intro-rule"></div>

  <div class="backdrop" role="img" aria-label="Faint illustration of a head in profile made of puzzle pieces"></div>

  <svg class="flow" width="1200" height="2253" viewBox="0 0 1200 2253" aria-hidden="true">
    <g fill="none" stroke="#cfcfcf" stroke-width="3" stroke-dasharray="9 7">
      <path d="M742 1020 C820 1080 840 1220 820 1335"/>
      <path d="M453 1332 C340 1390 330 1560 372 1650"/>
    </g>
    <circle cx="742" cy="1018" r="5" fill="#d4d4d4"/>
    <circle cx="453" cy="1331" r="5" fill="#d4d4d4"/>
    <path d="M812 1326l8 14 8-14z" fill="#cfcfcf"/>
    <path d="M364 1644l10 14 4-16z" fill="#cfcfcf"/>
  </svg>

  <!-- step 1 -->
  <span class="step-label" style="left:573px;top:951px;transform:rotate(6deg)">STEP 1</span>
  <div class="step-circle" style="left:530px;top:973px">
    <svg width="80" height="56" viewBox="0 0 80 56">
      <g fill="#666">
        <circle cx="10" cy="12" r="4"/><rect x="5" y="17" width="10" height="16" rx="2"/><rect x="6" y="33" width="3" height="12"/><rect x="11" y="33" width="3" height="12"/>
        <circle cx="24" cy="8" r="4"/><rect x="19" y="13" width="10" height="16" rx="2"/><rect x="20" y="29" width="3" height="12"/><rect x="25" y="29" width="3" height="12"/>
        <circle cx="56" cy="8" r="4"/><rect x="51" y="13" width="10" height="16" rx="2"/><rect x="52" y="29" width="3" height="12"/><rect x="57" y="29" width="3" height="12"/>
        <circle cx="70" cy="12" r="4"/><rect x="65" y="17" width="10" height="16" rx="2"/><rect x="66" y="33" width="3" height="12"/><rect x="71" y="33" width="3" height="12"/>
        <circle cx="40" cy="2" r="1.5"/><circle cx="33" cy="4" r="1.5"/><circle cx="47" cy="4" r="1.5"/>
      </g>
      <g fill="#f37122"><circle cx="40" cy="16" r="5"/><rect x="33" y="22" width="14" height="18" rx="2"/><rect x="34" y="40" width="4" height="15"/><rect x="42" y="40" width="4" height="15"/></g>
    </svg>
  </div>
  <h3 class="step-title" style="top:1136px">Shortlist Candidates</h3>
  <p class="step-text" style="top:1170px">Utilizing our user-friendly search options, find and<br>shortlist candidates within minutes You can also<br>contact us for any assitance</p>

  <!-- step 2 -->
  <div class="step-circle" style="left:533px;top:1270px">
    <svg width="54" height="56" viewBox="0 0 54 56">
      <rect x="3" y="7" width="48" height="46" rx="5" fill="none" stroke="#666" stroke-width="3.5"/>
      <rect x="14" y="1" width="4" height="11" fill="#666"/><rect x="36" y="1" width="4" height="11" fill="#666"/>
      <g fill="#f37122">
        <rect x="12" y="20" width="7" height="6"/><rect x="23" y="20" width="7" height="6"/><rect x="34" y="20" width="7" height="6"/>
        <rect x="12" y="30" width="7" height="6"/><rect x="23" y="30" width="7" height="6"/><rect x="34" y="30" width="7" height="6"/>
        <rect x="12" y="40" width="7" height="6"/><rect x="23" y="40" width="7" height="6"/><rect x="34" y="40" width="7" height="6"/>
      </g>
    </svg>
  </div>
  <span class="step-label" style="left:664px;top:1330px;transform:rotate(90deg)">STEP 2</span>
  <h3 class="step-title" style="top:1430px">Schedule Interview</h3>
  <p class="step-text" style="top:1462px">Send interview requests directly from our<br>platform or contact us.</p>

  <!-- step 3 -->
  <span class="step-label" style="left:488px;top:1656px;transform:rotate(-90deg)">STEP 3</span>
  <div class="step-circle" style="left:533px;top:1593px">
    <svg width="80" height="64" viewBox="0 0 80 64">
      <g fill="#666">
        <circle cx="10" cy="20" r="4"/><rect x="5" y="25" width="10" height="16" rx="2"/>
        <circle cx="24" cy="20" r="4"/><rect x="19" y="25" width="10" height="16" rx="2"/>
        <circle cx="56" cy="20" r="4"/><rect x="51" y="25" width="10" height="16" rx="2"/>
        <circle cx="70" cy="20" r="4"/><rect x="65" y="25" width="10" height="16" rx="2"/>
      </g>
      <g fill="#f37122"><circle cx="40" cy="12" r="5"/><rect x="34" y="18" width="12" height="20" rx="2"/><path d="M34 20L25 4l3-1 9 15zM46 20l9-16-3-1-9 15z"/><rect x="35" y="38" width="4" height="24"/><rect x="41" y="38" width="4" height="24"/></g>
    </svg>
  </div>
  <h3 class="step-title" style="top:1752px">Hire with Confidence</h3>
  <p class="step-text" style="top:1787px">Interview Candidates, negotiate offers and hire with<br>confidence. Upon request, TRAVENOK can run background<br>checks, drug screening and reference checks</p>
  <div class="pill"></div>
</main>

<footer class="site-footer">
  <div class="footer-brand">
    <div class="brand-name">TRAVENOK</div>
    <div class="brand-tag">Project Management Consulting</div>
  </div>
  <h4 class="footer-head" style="left:558px">Contact Us</h4>
  <div class="contact-row" style="top:87px">
    <svg width="9" height="13" viewBox="0 0 9 13" style="margin-top:5px"><path d="M4.5 0A4.5 4.5 0 0 0 0 4.5C0 8 4.5 13 4.5 13S9 8 9 4.5A4.5 4.5 0 0 0 4.5 0z" fill="#333"/><circle cx="4.5" cy="4.5" r="1.6" fill="#f3f3f3"/></svg>
    <span>418 Alder Crest Way, San Jose,<br>CA 95121.</span>
  </div>
  <div class="contact-row" style="top:134px">
    <svg width="11" height="9" viewBox="0 0 11 9" style="margin-top:8px"><rect width="11" height="9" fill="#333"/><path d="M0 0l5.5 5L11 0" stroke="#f3f3f3" fill="none"/></svg>
    <span>Email: office@travenoktech.example</span>
  </div>
  <h4 class="footer-head" style="left:912px">Follow Us</h4>
  <div class="footer-rule"></div>
  <p class="copyright">Copyrihgts @ 2016 All Rights Reserved</p>
</footer>

<span class="social" style="left:912px" role="img" aria-label="Social profile link"></span>
<span class="social" style="left:967px;border-color:#5bb3e6" role="img" aria-label="Social profile link"></span>
<span class="social" style="left:1024px;border-color:#3a3f9e" role="img" aria-label="Social profile link"></span>

</body>
</html>
```